Systems and Technology Consultants - Website

Design & Build a website for a new company which operates in the Systems and Technology space for Transportation, Government and Commercial sectors.

Overall design should be minimalist in nature.
Should also have a feed that provides news and event updates on the main page.
Logo has already been awarded and should be incorporated into the site.

We like the overall layout, functionality and simplicity of the below sites. Submitted designs could be similar to or a combination of the aspects on these sites, or perhaps a whole different concept - we are open to new ideas.
Norvique.com
Teblo.it

Update 1 Dated 27 May 2014

All I am moving away from the Teblo.it website and would like it to be more aligned with Norvique.com not only in layout but in functionality. I will be extending the deadline of this design brief for two weeks to incorporate additional requirements and will add addtional funding to the project.

Apologies for not having more information available to provide but with so many submissions its getting confusing.

Thanks Derek

Please note that the brief has been updated and the deadline has been extended.

Important: We will need two language versions of the website, English and Arabic; the website is hosted on HostPelican

Hello All, Thank you for your submissions. We have narrowed it down to the final 6 designers and I just wanted to take a moment and provide a bit of feedback regarding the concepts that we like and the modifications we are looking for. First, let me mention some of the design functions we like. - At the top of the homepage we really like the "region" or "language" tab so that the website can be viewed in both English and Arabic. - We like the homepage to have clear color variation so that the different sections of the homepage are distinct. Additionally, we like the bottom portion of the homepage to be in red. We feel that draws attention to our contact information. Again, we would like the colors to integrate black, gray-scale, red, etc. - Having a search tab at the top of the home page, or integrated into the main image, so that the site is easy to navigate. - We especially like the main image to have the scrolling tabs at the bottom so it is easy to browse the services offered (Consultancy, Solutions Architecture, Masters Systems Integration, Independent Design Review). - In regards to the services offered tab we really like the idea that a few people presented that have the outside of our logo with an icon in the middle of consultancy, solutions, etc., etc. Secondly, as mentioned in our brief we really enjoy the design of norvique site. Specially, we enjoy the strong iconic images they use, the way the tabs at the top scroll easily, and contact us page that generates an email. Lastly, I've included some photos of the concept we have been working on. What we are trying to demonstrate is how our company offers a range of services that are essentially linked together. We provide individual services that when combined present the full service package. We would like this concept to be integrated into the over concept of our website. Please feel free to ask for clarification of any of the above points or contact us if you have any additional questions. We appreciate all of your hard work and are very excited to see the updated designs. Best, Marta Vennick Quelbrant Senior Program Manager marta.vennick@quelbrant-example.com

Industry/Entity Type

Government

Font styles to use
Serif
Sans Serif

Requirements
Must have
• Must work on/adapt to various/mobile devices (responsive)
Must be simple and straightforward
Colors should be in line/matching with logo
2 language versions: English and Arabic (no Thai)
Services should be the first group/row of items after/below the main image
Note: the website will be hosted by hostpelican
Nice to have
• Submit feedback form
What's New section
The banner at the bottom of the site should not be too large; we would like a narrow one more
It would be nice if the header/top banner (with Home, About, etc. tabs) could stay in place as you scroll down (like Norvique and Chatterloop)
We will likely only use one image with a Company slogan on the Home page rather than a carousel of images to rotate through
Should not have
• This is the existing website: http://www.quelbrant-example.org
We do not like the animation, the way the banner icons/titles bounce
Not simple enough, we don't like the functionality or how pages load so slowly
We do not like the logo centered - it should be at the left
The banner and its tabs should not be towards the right, we would like them to be centered, to go all the way across and to be below the logo

```html
<!DOCTYPE html>
<html lang="en">
<head>
<meta charset="utf-8">
<title>Quelbrant – Systems and Technology Consultants</title>
<link href="https://fonts.googleapis.com/css2?family=Roboto+Condensed:wght@400;700&family=Arimo:wght@400;700&display=swap" rel="stylesheet">
<style>
:root{
  --red:#e81f28;
  --red-dark:#c9141c;
  --ink:#3a3a3a;
  --muted:#8c8c8c;
  --tile:#f1f1f1;
  --band:#f6f5f6;
  --black:#141414;
  --white:#ffffff;
}
*{box-sizing:border-box;margin:0;padding:0}
html,body{width:799px;height:1200px;overflow:hidden;background:var(--white)}
body{position:relative;font-family:"Arimo",Arial,sans-serif;color:var(--ink)}
.abs{position:absolute}

/* header */
.brand{left:143px;top:40px;display:flex;align-items:center;gap:8px}
.brand-mark{width:16px;height:16px;background:var(--red)}
.brand-name{font-family:"Roboto Condensed",sans-serif;font-weight:700;font-size:26px;letter-spacing:3px;color:var(--red)}
.top-phone{left:482px;top:48px;display:flex;align-items:center;gap:6px;font-size:8px;color:var(--ink)}
.search{left:570px;top:46px;width:86px;height:18px;border:1px solid #d6d6d6;font-size:7px;color:var(--muted);padding:4px 6px}
.search svg{position:absolute;right:5px;top:4px}
.main-nav{left:0;top:87px;width:656px;display:flex;justify-content:flex-end}
.main-nav a{font-family:"Roboto Condensed",sans-serif;font-weight:700;font-size:9px;color:var(--ink);text-decoration:none;margin-left:26px}
.main-nav a.active{color:var(--red)}

/* hero */
.hero{left:0;top:128px;width:799px;height:254px;background:linear-gradient(100deg,#d9d9d9 0%,#ececec 45%,#cfcfcf 100%)}
.hero-title{left:143px;top:193px;width:320px;font-family:"Roboto Condensed",sans-serif;font-weight:700;font-size:13.5px;line-height:18px;color:var(--red);white-space:nowrap}
.btn{height:26px;display:flex;align-items:center;justify-content:center;font-family:"Roboto Condensed",sans-serif;font-weight:700;font-size:9.5px;color:var(--white);border-radius:3px}
.btn-red{left:143px;top:273px;width:92px;background:linear-gradient(#f2444b,var(--red-dark))}
.btn-dark{left:249px;top:273px;width:91px;background:linear-gradient(#5b5b5b,#333)}
.hero-portrait{left:451px;top:143px;width:203px;height:239px;background:linear-gradient(180deg,#9a8a80 0%,#2a3547 35%,#1c2536 100%);border-radius:40px 40px 0 0}

/* services */
.service{width:104px;text-align:center}
.service .icon{width:40px;height:38px;margin:0 auto;background:var(--tile);display:flex;align-items:center;justify-content:center}
.service p{margin-top:10px;font-family:"Roboto Condensed",sans-serif;font-size:7px;color:#666;white-space:nowrap}
.divider{left:240px;top:592px;width:320px;height:1px;background:linear-gradient(90deg,transparent,#ddd,transparent)}

/* about */
.section-title{left:0;top:619px;width:799px;text-align:center;font-family:"Roboto Condensed",sans-serif;font-weight:700;font-size:15px;color:var(--red)}
.about-photo{left:143px;top:661px;width:246px;height:138px;background:linear-gradient(120deg,#c7cfd8 0%,#e9e3dc 40%,#9fb3c6 100%)}
.about-text{left:408px;top:659px;width:248px;font-size:7px;line-height:11.2px;color:var(--muted);text-align:justify}
.read-more{left:408px;top:781px;width:56px;height:18px;background:var(--tile);font-size:7px;color:#666;display:flex;align-items:center;justify-content:center}

/* feed */
.feed{left:0;top:828px;width:799px;height:215px;background:var(--band)}
.feed-title{font-family:"Roboto Condensed",sans-serif;font-weight:700;font-size:10px;color:var(--ink)}
.event-thumb{width:56px;height:48px;border:2px solid var(--white);box-shadow:0 0 0 1px #ddd;background:linear-gradient(135deg,#dfe7ef,#9bb6cc)}
.feed-text{width:176px;font-size:7px;line-height:11px;color:var(--muted)}
.date{width:45px;height:38px;background:var(--red);color:var(--white);text-align:center;padding-top:7px}
.date b{display:block;font-family:"Roboto Condensed",sans-serif;font-size:11px}
.date span{font-size:6.5px}
.news-head{font-family:"Roboto Condensed",sans-serif;font-weight:700;font-size:9.5px;color:#555}

/* footer */
.site-footer{left:0;top:1043px;width:799px;height:131px;background:var(--red)}
.foot-col{top:1064px;font-size:7px;line-height:11.5px;color:var(--white)}
.foot-col h4{font-family:"Roboto Condensed",sans-serif;font-weight:400;font-size:8.5px;margin-bottom:6px}
.socials{display:flex;gap:4px;margin-top:4px}
.socials i{display:block;width:14px;height:14px;background:var(--white)}
.newsletter-label{margin-top:6px;font-family:"Roboto Condensed",sans-serif;font-size:8.5px}
.newsletter{left:542px;top:1121px;width:114px;height:16px;background:var(--white);font-size:7px;color:#444;padding:4px 5px}
.newsletter span{position:absolute;right:3px;top:2px;height:12px;padding:0 4px;background:var(--red);color:var(--white);font-size:6.5px;line-height:12px}
.copyright{left:0;top:1174px;width:799px;height:26px;background:var(--black);color:#ddd;font-size:6.5px;text-align:center;line-height:26px}
</style>
</head>
<body>

<header>
  <div class="abs brand"><span class="brand-mark"></span><span class="brand-name">QUELBRANT</span></div>
  <div class="abs top-phone">
    <svg width="11" height="9" viewBox="0 0 11 9"><path d="M1 3 Q5.5 -1 10 3 L8.5 4.5 L7 3.5 L7 2.5 Q5.5 2 4 2.5 L4 3.5 L2.5 4.5Z" fill="#e81f28"/><rect x="2.5" y="5" width="6" height="3.5" rx="1" fill="#e81f28"/></svg>
    +(00)-02-555-0148
  </div>
  <div class="abs search">Search
    <svg width="9" height="9" viewBox="0 0 9 9"><circle cx="3.6" cy="3.6" r="2.6" fill="none" stroke="#aaa" stroke-width="1.1"/><path d="M5.5 5.5 L8 8" stroke="#aaa" stroke-width="1.2"/></svg>
  </div>
  <nav class="abs main-nav">
    <a class="active" href="#">Home</a><a href="#">Business unit</a><a href="#">Services</a><a href="#">About us</a><a href="#">Location</a><a href="#">Contact us</a>
  </nav>
</header>

<section>
  <div class="abs hero" role="img" aria-label="Light grey abstract technology background with circuit lines"></div>
  <h1 class="abs hero-title">Quelbrant specializes in delivering quality professional<br>services and technical projects that support<br>larger business goals.</h1>
  <a class="abs btn btn-red">Latest Projects</a>
  <a class="abs btn btn-dark">Quick &nbsp;solution</a>
  <div class="abs hero-portrait" role="img" aria-label="Photo of a businessman in a dark suit with arms crossed"></div>
</section>

<section class="services">
  <div class="abs service" style="left:137px;top:410px"><div class="icon"><svg width="16" height="16" viewBox="0 0 16 16"><circle cx="6" cy="6" r="3.5" fill="none" stroke="#777" stroke-width="2.2" stroke-dasharray="2 1.2"/><circle cx="11.5" cy="11.5" r="2.2" fill="none" stroke="#777" stroke-width="1.6"/></svg></div><p>Systems Design &amp; Engineering</p></div>
  <div class="abs service" style="left:241px;top:410px"><div class="icon"><svg width="16" height="14" viewBox="0 0 16 14"><rect x="1" y="4" width="14" height="9" rx="1" fill="#777"/><rect x="5.5" y="1.5" width="5" height="3" fill="none" stroke="#777" stroke-width="1.3"/></svg></div><p>Systems Project Management</p></div>
  <div class="abs service" style="left:346px;top:410px"><div class="icon"><svg width="16" height="16" viewBox="0 0 16 16"><path d="M2 14 L7 9" stroke="#777" stroke-width="2"/><path d="M3 6 Q3 13 10 13 Z" fill="#777"/><path d="M9 3 A4 4 0 0 1 13 7 M9 0.5 A6.5 6.5 0 0 1 15.5 7" fill="none" stroke="#777" stroke-width="1.3"/></svg></div><p>Radio Area Networks</p></div>
  <div class="abs service" style="left:451px;top:410px"><div class="icon"><svg width="16" height="16" viewBox="0 0 16 16"><g fill="none" stroke="#777" stroke-width="1"><ellipse cx="8" cy="8" rx="7" ry="2.6"/><ellipse cx="8" cy="8" rx="7" ry="2.6" transform="rotate(60 8 8)"/><ellipse cx="8" cy="8" rx="7" ry="2.6" transform="rotate(-60 8 8)"/></g><circle cx="8" cy="8" r="1.3" fill="#777"/></svg></div><p>Systems Construction Management</p></div>
  <div class="abs service" style="left:556px;top:410px"><div class="icon"><svg width="16" height="16" viewBox="0 0 16 16"><path d="M8 1 L9 6 L15 9 L15 10 L9 8.5 L8.8 12.5 L10.5 14 L10.5 15 L8 14 L5.5 15 L5.5 14 L7.2 12.5 L7 8.5 L1 10 L1 9 L7 6 Z" fill="#777"/></svg></div><p>Special Airport Systems</p></div>

  <div class="abs service" style="left:137px;top:509px"><div class="icon"><svg width="14" height="16" viewBox="0 0 14 16"><path d="M3.5 7 V4.5 A3.5 3.5 0 0 1 10.5 4.5 V7" fill="none" stroke="#777" stroke-width="1.8"/><rect x="1.5" y="7" width="11" height="8" rx="1" fill="#777"/></svg></div><p>Security Systems</p></div>
  <div class="abs service" style="left:241px;top:509px"><div class="icon"><svg width="14" height="17" viewBox="0 0 14 17"><rect x="1.5" y="1" width="11" height="12" rx="2" fill="none" stroke="#777" stroke-width="1.6"/><rect x="3.5" y="3" width="7" height="4" fill="#777"/><circle cx="4.5" cy="10" r="1" fill="#777"/><circle cx="9.5" cy="10" r="1" fill="#777"/><path d="M3 16 L5 13 M11 16 L9 13" stroke="#777" stroke-width="1.4"/></svg></div><p>Rail Systems</p></div>
  <div class="abs service" style="left:346px;top:509px"><div class="icon"><svg width="18" height="14" viewBox="0 0 18 14"><path d="M1 4.5 H4 L8 1 V13 L4 9.5 H1 Z" fill="#777"/><path d="M10.5 4.5 Q12 7 10.5 9.5 M13 2.5 Q16 7 13 11.5" fill="none" stroke="#777" stroke-width="1.3"/></svg></div><p>Wireless Construction</p></div>
  <div class="abs service" style="left:451px;top:509px"><div class="icon"><svg width="14" height="17" viewBox="0 0 14 17"><path d="M5 1 H9 M5.5 1 V6.5 L1.5 15 H12.5 L8.5 6.5 V1" fill="none" stroke="#777" stroke-width="1.3"/><path d="M3.3 11 H10.7 L12.5 15 H1.5 Z" fill="#777"/></svg></div><p>Oil &amp; Gas Systems</p></div>
  <div class="abs service" style="left:556px;top:509px"><div class="icon"><svg width="10" height="16" viewBox="0 0 10 16"><rect x="1" y="1" width="8" height="14" rx="1.5" fill="none" stroke="#777" stroke-width="1.4"/><circle cx="5" cy="12.6" r="0.9" fill="#777"/></svg></div><p>Cellular Construction</p></div>
  <div class="abs divider"></div>
</section>

<section class="about">
  <h2 class="abs section-title">Something About us</h2>
  <div class="abs about-photo" role="img" aria-label="Photo of a smiling team gathered around a laptop"></div>
  <p class="abs about-text">Lorem Ipsum is simply dummy text of the printing and typesetting industry. Lorem Ipsum has been the industry's standard dummy text ever since the 1500s, when an unknown printer took a galley of type and scrambled it to make a type specimen book. It has survived not only five centuries, but also the leap into electronic typesetting, remaining essentially unchanged. It was popularised in the 1960s with the release of Tracelet sheets containing Lorem Ipsum passages, and more recently with desktop publishing software like Vellum PageSetter including versions of Lorem Ipsum.</p>
  <a class="abs read-more">Read more</a>
</section>

<section>
  <div class="abs feed"></div>
  <h3 class="abs feed-title" style="left:143px;top:856px">Latest Events</h3>
  <div class="abs event-thumb" style="left:143px;top:882px" role="img" aria-label="Photo of hands reviewing printed charts"></div>
  <p class="abs feed-text" style="left:213px;top:880px">Lorem Ipsum is simply dummy text of the printing and typesetting industry. Lorem Ipsum has been the industry's standard dummy text ever since the 1500s, when an ul.r-sions of Lorem Ipsum.</p>
  <div class="abs event-thumb" style="left:143px;top:948px" role="img" aria-label="Photo of a hand pointing at a chart on a tablet"></div>
  <p class="abs feed-text" style="left:213px;top:946px">Lorem Ipsum is simply dummy text of the printing and typesetting industry. Lorem Ipsum has been the industry's standard dummy text ever since the 1500s, when an Lr-sions of Lorem Ipsum.</p>

  <h3 class="abs feed-title" style="left:408px;top:856px">Latest News</h3>
  <div class="abs date" style="left:408px;top:882px"><b>MAY 17</b><span>2014</span></div>
  <h4 class="abs news-head" style="left:476px;top:881px">News headline goes here</h4>
  <p class="abs feed-text" style="left:476px;top:898px">typesetting industry. Lorem Ipsum has been the industry's standard dummy text ever since the 1500s, when an ul.r-sions of Lorem Ipsum.</p>
  <div class="abs date" style="left:408px;top:948px"><b>MAY 17</b><span>2014</span></div>
  <h4 class="abs news-head" style="left:476px;top:946px">News headline goes here</h4>
  <p class="abs feed-text" style="left:476px;top:964px">typesetting industry. Lorem Ipsum has been the industry's standard dummy text ever since the 1500s, when an ul.r-sions of Lorem Ipsum.</p>
</section>

<footer>
  <div class="abs site-footer"></div>
  <div class="abs foot-col" style="left:143px"><h4>QUICK LINKS</h4>Home<br>About us<br>Services<br>Privacy policy<br>terms of use<br>Contact us</div>
  <div class="abs foot-col" style="left:275px"><h4>SERVICES</h4>Consulting<br>Engineering<br>Construction<br>Operation<br>Maintenance</div>
  <div class="abs foot-col" style="left:408px"><h4>CONTACT US</h4>Phone : &nbsp;+(00)-02-555-0148<br>Email &nbsp;: info@quelbrant-example.org<br>Mailling Address :<br>12 meadowline rd, eastfield,<br>harbor city 40120</div>
  <div class="abs foot-col" style="left:542px"><h4>SOCIAL MEDIA LINKS</h4><div class="socials"><i></i><i></i><i></i></div><div class="newsletter-label">Newsletter Signup</div></div>
  <div class="abs newsletter">Enter your email<span>Sign up</span></div>
  <div class="abs copyright">Copyright 2013-2014 www.quelbrant-example.biz All rights reserved</div>
</footer>

</body>
</html>
```